TWPC Business Card Design

Business card for sole operator professional civil and traffic engineer.
Clients are developers and planners who require assistance with traffic strategic master planning advice and design development for access and infrastructure associated with the development.
Colours already in use are greens for the business name and black for other legend. The attached file shows the letterhead template which is currently in use.
Target Market(s)
Professional Clients in development industry
Most clients known to the Principal and card is mostly required to allow ongoing contact
Industry/Entity Type
Business
Contact Information for Business Card
LACHLAN PETTIGREW CONSULTING PARTNERS
ABN 37 814 529 106
PO Box 418 KELWOOD NSW 2619
Lachlan Pettigrew 0412 358 971
l.pettigrew@corvanmail.net

```html
<!DOCTYPE html>
<html lang="en">
<head>
<meta charset="utf-8">
<title>TWPC Business Card</title>
<link rel="stylesheet" href="https://fonts.googleapis.com/css2?family=Arimo:wght@400&display=swap">
<style>
  :root {
    --page-bg: #d9d6d2;
    --card-bg: #ffffff;
    --band: #050505;
    --brand-green: #8cc63f;
    --ink: #1a1a1a;
  }
  html, body {
    margin: 0;
    padding: 0;
    width: 1200px;
    height: 848px;
    overflow: hidden;
    background: var(--page-bg);
    font-family: "Arimo", Arial, sans-serif;
  }
  .card {
    position: absolute;
    left: 100px;
    top: 118px;
    width: 1000px;
    height: 611px;
    background: var(--card-bg);
    border-radius: 40px;
    overflow: hidden;
    box-shadow: 0 10px 30px rgba(0,0,0,0.18);
  }
  .principal {
    position: absolute;
    left: 70px;
    top: 58px;
    margin: 0;
    font-size: 26px;
    font-weight: 400;
    color: var(--brand-green);
    letter-spacing: 0.5px;
  }
  .abn {
    position: absolute;
    left: 70px;
    top: 92px;
    margin: 0;
    font-size: 24px;
    color: var(--ink);
  }
  .name-band {
    position: absolute;
    left: 0;
    right: 0;
    top: 172px;
    height: 118px;
    background: var(--band);
    display: flex;
    align-items: center;
    justify-content: flex-end;
    padding-right: 46px;
  }
  .business-name {
    margin: 0;
    font-size: 35px;
    font-weight: 400;
    color: var(--brand-green);
    letter-spacing: 0.3px;
    white-space: nowrap;
  }
  .contact-list {
    position: absolute;
    right: 40px;
    top: 400px;
    margin: 0;
    padding: 0;
    list-style: none;
  }
  .contact-item {
    display: flex;
    align-items: center;
    justify-content: flex-end;
    height: 44px;
    font-size: 25px;
    color: var(--ink);
  }
  .contact-item .value { margin-right: 22px; }
  .contact-item svg { width: 28px; height: 28px; fill: var(--brand-green); }
</style>
</head>
<body>
  <section class="card">
    <h2 class="principal">LACHLAN PETTIGREW</h2>
    <p class="abn">ABN 37 814 529 106</p>

    <div class="name-band">
      <h1 class="business-name">LACHLAN PETTIGREW CONSULTING PARTNERS</h1>
    </div>

    <ul class="contact-list">
      <li class="contact-item">
        <span class="value">0412 358 971</span>
        <svg viewBox="0 0 24 24" aria-hidden="true">
          <path d="M3 9c0-3 4-5 9-5s9 2 9 5v2h-5V9c-1-.6-2.4-1-4-1s-3 .4-4 1v2H3z"/>
          <path d="M6 12h12l2 8H4z M12 14a2.5 2.5 0 1 0 0 5a2.5 2.5 0 1 0 0-5z" fill-rule="evenodd"/>
        </svg>
      </li>
      <li class="contact-item">
        <span class="value">l.pettigrew@corvanmail.net</span>
        <svg viewBox="0 0 24 24" aria-hidden="true">
          <path d="M2 5h20v14H2z M3.5 6.5L12 13l8.5-6.5" fill-rule="evenodd"/>
          <path d="M3 6l9 7 9-7" fill="none" stroke="#fff" stroke-width="1.4"/>
        </svg>
      </li>
      <li class="contact-item">
        <span class="value">418 KELWOOD NSW 2619</span>
        <svg viewBox="0 0 24 24" aria-hidden="true">
          <path d="M12 2a7 7 0 0 0-7 7c0 5 7 13 7 13s7-8 7-13a7 7 0 0 0-7-7zm0 4a3 3 0 1 1 0 6a3 3 0 1 1 0-6z" fill-rule="evenodd"/>
        </svg>
      </li>
    </ul>
  </section>
</body>
</html>
```